Kinesiology undergraduate program needs an infographic

We would like an infographic to creatively and succinctly inform students, faculty, staff, and others about our undergraduate values and competencies (perhaps also integrating our mission and vision). We would like to see a design that incorporates the definition of Kinesiology (the study of human movement) and the colors of our Westbrook State University at Harlan.

```html
<!DOCTYPE html>
<html lang="en">
<head>
<meta charset="utf-8">
<title>The Science of Kinesiology – Westbrook State University at Harlan</title>
<link href="https://fonts.googleapis.com/css2?family=Montserrat:wght@500;600;700;800&display=swap" rel="stylesheet">
<style>
  :root{
    --cyan:#1ba3c8;
    --navy:#101d52;
    --olive:#7b901d;
    --red:#d3173d;
    --orange:#e9961f;
    --white:#ffffff;
    --ink:#1d2a4a;
  }
  *{box-sizing:border-box;margin:0;padding:0}
  html,body{width:678px;height:1200px;overflow:hidden;background:var(--white)}
  body{font-family:"Montserrat",Arial,sans-serif;color:var(--ink)}
  .infographic{position:relative;width:678px;height:1200px}

  /* top split */
  .science{position:absolute;left:0;top:0;width:339px;height:628px;background:var(--cyan);color:var(--white)}
  .screen{position:absolute;left:38px;top:18px;width:260px;height:215px;background:linear-gradient(180deg,#f4f5f7,#dfe3e8);border:6px solid #c9ced6;border-top-width:10px}
  .screen-figures{position:absolute;left:26px;top:16px;right:26px;bottom:16px;background:linear-gradient(90deg,#d98a6a,#c4554a 50%,#d98a6a);opacity:.55;border-radius:40px}
  .tripod{position:absolute;left:0;top:0}
  .science-title{position:absolute;left:40px;top:314px;font-size:29px;font-weight:800;line-height:1.15}
  .science-list{position:absolute;left:40px;top:382px;list-style:none}
  .science-list li{display:flex;align-items:center;height:80px;font-size:15px;font-weight:600;line-height:1.25;white-space:nowrap}
  .science-list .icon{flex:0 0 46px;height:46px;margin-right:20px}

  .block{position:absolute;left:339px;width:339px;color:var(--white);display:flex;padding:0 14px 0 22px}
  .block .icon{flex:0 0 58px;height:58px;border-radius:50%;margin-right:16px;align-self:center}
  .block h2{font-size:19px;font-weight:800;margin-bottom:2px}
  .block p,.block li{font-size:11.5px;font-weight:500;line-height:1.35}
  .block ul{list-style:none;margin-top:2px}
  .block li::before{content:"\2022";margin-right:6px}
  .mission{top:0;height:155px;background:var(--navy);padding-top:22px}
  .mission .icon{align-self:flex-start;margin-top:20px}
  .vision{top:155px;height:95px;background:var(--olive);align-items:center}
  .values{top:250px;height:107px;background:var(--red);align-items:center}

  .thinking{position:absolute;left:339px;top:357px;width:339px;height:271px;background:var(--white)}
  .thinking h2{margin-top:40px;text-align:center;font-size:29px;font-weight:800;line-height:1.15;color:var(--cyan)}
  .skill-grid{display:grid;grid-template-columns:1fr 1fr;row-gap:18px;padding:22px 10px 0 24px}
  .skill{display:flex;align-items:center;font-size:13.5px;font-weight:600;line-height:1.2;color:var(--ink);white-space:nowrap}
  .skill .icon{flex:0 0 48px;height:48px;border-radius:50%;margin-right:10px}

  /* bands */
  .band{position:absolute;left:0;width:678px;color:var(--white);text-align:center}
  .band h2{font-size:30px;font-weight:800;line-height:1.15}
  .relationships{top:628px;height:297px;background:var(--orange);padding-top:40px}
  .growth{top:925px;height:275px;background:var(--navy);padding-top:36px}
  .row{display:flex;justify-content:space-around;padding:0 8px}
  .item{display:flex;flex-direction:column;align-items:center;font-size:13.5px;font-weight:600;line-height:1.25;white-space:nowrap}
  .item .icon{width:62px;height:62px;border-radius:50%;margin-bottom:16px}
  .relationships .row{margin-top:44px}
  .growth .row{margin-top:38px}
</style>
</head>
<body>
<main class="infographic">

  <section class="science">
    <div class="screen">
      <div class="screen-figures" role="img" aria-label="Anatomical muscle figures shown on a presentation screen"></div>
    </div>
    <svg class="tripod" width="339" height="320" viewBox="0 0 339 320" aria-hidden="true">
      <g stroke="#3a3f4a" stroke-width="4" stroke-linecap="round" fill="none">
        <line x1="168" y1="4" x2="168" y2="18"/>
        <line x1="168" y1="233" x2="168" y2="300"/>
        <line x1="168" y1="262" x2="130" y2="302"/>
        <line x1="168" y1="262" x2="206" y2="302"/>
      </g>
    </svg>
    <h1 class="science-title">The Science of<br>Kinesiology</h1>
    <ul class="science-list">
      <li><span class="icon" role="img" aria-label="Human body icon" style="background:#e04a2f;border-radius:18px 18px 6px 6px"></span>Foundational<br>Concepts of<br>Kinesiology</li>
      <li><span class="icon" role="img" aria-label="Clinical kit icon" style="background:#f2b233;border-radius:8px"></span>Clinical<br>Application</li>
      <li><span class="icon" role="img" aria-label="Atom icon" style="background:#f0e6c8;border-radius:50%"></span>Scientific<br>Communication</li>
    </ul>
  </section>

  <section class="block mission">
    <span class="icon" role="img" aria-label="Rocket icon" style="background:#e8edf5"></span>
    <div>
      <h2>Our Mission</h2>
      <p>To empower undergraduate students<br>to pursue excellence through</p>
      <ul>
        <li>Scientific Discovery</li>
        <li>Clinical Practice</li>
        <li>Health Promotion</li>
      </ul>
    </div>
  </section>

  <section class="block vision">
    <span class="icon" role="img" aria-label="Light bulb icon" style="background:#f3c43a"></span>
    <div>
      <h2>Our Vision</h2>
      <p>WSUH Kinesiology graduates are leaders who excel in careers that enhance the quality of life of individuals and communities.</p>
    </div>
  </section>

  <section class="block values">
    <span class="icon" role="img" aria-label="Hands holding a heart icon" style="background:#f1a07a"></span>
    <div>
      <h2>Our Values</h2>
      <ul>
        <li>Student Success</li>
        <li>Science</li>
        <li>Service</li>
      </ul>
    </div>
  </section>

  <section class="thinking">
    <h2>Thinking and<br>Reasoning</h2>
    <div class="skill-grid">
      <div class="skill"><span class="icon" role="img" aria-label="Thinking head icon" style="background:#e2463a"></span>Critical<br>Thinking</div>
      <div class="skill"><span class="icon" role="img" aria-label="Microscope icon" style="background:#2d5fa8"></span>Scientific<br>Inquiry</div>
      <div class="skill"><span class="icon" role="img" aria-label="Brain with numbers icon" style="background:#f08a8a"></span>Quantitative<br>Reasoning</div>
      <div class="skill"><span class="icon" role="img" aria-label="Gears and ideas icon" style="background:#2e9ad0"></span>Concept<br>Integration</div>
    </div>
  </section>

  <section class="band relationships">
    <h2>Relationships and<br>Communication</h2>
    <div class="row">
      <div class="item"><span class="icon" role="img" aria-label="Hand holding a heart icon" style="background:#f06a5a"></span>Cultural<br>Competence</div>
      <div class="item"><span class="icon" role="img" aria-label="Service handbook icon" style="background:#1f2f5a;border-radius:6px"></span>Service Orientation<br>or Citizenship</div>
      <div class="item"><span class="icon" role="img" aria-label="Team of people icon" style="background:#3a6fb8"></span>Leadership and<br>Teamwork</div>
      <div class="item"><span class="icon" role="img" aria-label="Professional person icon" style="background:#2f5d9a"></span>Professionalism</div>
    </div>
  </section>

  <section class="band growth">
    <h2>Intrapersonal<br>Growth</h2>
    <div class="row">
      <div class="item"><span class="icon" role="img" aria-label="Growth steps chart icon" style="background:#3bb273;border-radius:6px"></span>Cultural Humility<br>or Sensitivity</div>
      <div class="item"><span class="icon" role="img" aria-label="Balance scale icon" style="background:#e3a93a"></span>Integrity</div>
      <div class="item"><span class="icon" role="img" aria-label="Handshake icon" style="background:#5b8fd6"></span>Self-Directed</div>
      <div class="item"><span class="icon" role="img" aria-label="Circular arrows icon" style="background:#e4573d"></span>Dependability</div>
      <div class="item"><span class="icon" role="img" aria-label="Mountain flag icon" style="background:#8ba0c0"></span>Mission<br>Oriented</div>
    </div>
  </section>

</main>
</body>
</html>
```